Business card design

I need my logo on this card, things I need the card to have on it
licensed and insured.
owner operators Milo & Trent Halvorsen
my phone number 5083716254
Disaster Recovery, Storm Damage Restoration, Proactive Disaster Plan Management, Roof Repair/Restoration Structural Repair and Reconstruction, Emergency Boarding and Tarping Service, Perimeter Fencing, Emergency Tree Removal,

```html
<!DOCTYPE html>
<html lang="en">
<head>
<meta charset="utf-8">
<title>Halvorsen's Construction – Business Cards</title>
<link href="https://fonts.googleapis.com/css2?family=Michroma&family=Nunito+Sans:wght@400;700&display=swap" rel="stylesheet">
<style>
  :root {
    --backdrop: #ebebeb;
    --card-blue: #0f85b5;
    --ink-white: #ffffff;
    --ghost-white: rgba(255, 255, 255, 0.16);
  }
  * { box-sizing: border-box; margin: 0; padding: 0; }
  html, body {
    width: 1200px;
    height: 1200px;
    overflow: hidden;
    background: var(--backdrop);
  }
  .sheet {
    width: 1200px;
    height: 1200px;
    display: flex;
    flex-direction: column;
    align-items: center;
    justify-content: center;
    gap: 56px;
  }
  .card {
    position: relative;
    width: 900px;
    height: 514px;
    background: var(--card-blue);
    color: var(--ink-white);
    overflow: hidden;
    font-family: "Nunito Sans", sans-serif;
  }

  /* Back side: contact details and services */
  .brand-small {
    position: absolute;
    left: 62px;
    top: 58px;
    display: flex;
    align-items: center;
    gap: 10px;
    font-size: 17px;
    font-weight: 400;
    letter-spacing: 0.02em;
  }
  .brand-small .brand-square {
    width: 14px;
    height: 14px;
    background: var(--ink-white);
  }
  .ghost-square {
    position: absolute;
    right: 40px;
    top: 40px;
    width: 150px;
    height: 150px;
    background: var(--ghost-white);
  }
  .owners {
    position: absolute;
    left: 62px;
    top: 176px;
  }
  .owners-name {
    font-family: "Michroma", sans-serif;
    font-size: 31px;
    letter-spacing: 0.01em;
    text-transform: uppercase;
    line-height: 1.1;
  }
  .owners-role {
    font-size: 21px;
    font-weight: 700;
    margin-top: 6px;
  }
  .owners-phone {
    font-size: 19px;
    margin-top: 2px;
    margin-left: 4px;
  }
  .services {
    position: absolute;
    left: 78px;
    top: 316px;
    list-style: none;
    font-size: 18px;
    line-height: 1.34;
  }

  /* Front side: centred brand name */
  .card-front {
    display: flex;
    align-items: center;
    justify-content: center;
  }
  .brand-large {
    display: flex;
    align-items: center;
    gap: 22px;
    font-size: 52px;
    font-weight: 400;
    letter-spacing: 0.02em;
  }
  .brand-large .brand-square {
    width: 40px;
    height: 40px;
    background: var(--ink-white);
  }
</style>
</head>
<body>
  <main class="sheet">
    <section class="card card-back" aria-label="Business card, back">
      <div class="brand-small"><span class="brand-square"></span><span>Halvorsen's Construction L.L.C</span></div>
      <div class="ghost-square" aria-hidden="true"></div>
      <div class="owners">
        <h1 class="owners-name">Milo &amp; Trent Halvorsen</h1>
        <p class="owners-role">Owner Operator</p>
        <p class="owners-phone">P: (508) 371-6254</p>
      </div>
      <ul class="services">
        <li>Disaster Recovery</li>
        <li>Perimeter Fencing</li>
        <li>Roof Repair/Restoration</li>
        <li>Emergency Tree Removal</li>
        <li>Storm Damage Restoration</li>
        <li>Proactive Disaster Plan Management</li>
        <li>Structural Repair and Reconstruction</li>
        <li>Emergency Boarding and Tarping Service</li>
      </ul>
    </section>

    <section class="card card-front" aria-label="Business card, front">
      <div class="brand-large"><span class="brand-square"></span><span>Halvorsen's Construction L.L.C</span></div>
    </section>
  </main>
</body>
</html>
```